I need a SEO-friendly Wordpress website (making sure to style H1, H2, H3, etc correctly) for a Hawaii-based law firm called Meridian Crest Legal Group. Comparable websites include https://brvlaw.example/ and https://www.lomrit.example/ for design reference. The current copy on the TarnAdvocate.example website can be used.

```html
<!DOCTYPE html>
<html lang="en">
<head>
<meta charset="utf-8">
<title>Meridian Crest Legal Group</title>
<link rel="stylesheet" href="https://fonts.googleapis.com/css2?family=Montserrat:wght@400;500;600;700;800&display=swap">
<style>
:root{
  --brown:#84290b;
  --rust:#b4501b;
  --accent:#c0550f;
  --ink:#1d1d1d;
  --text:#444;
  --muted:#8a8a8a;
  --faint:#fcefe7;
  --line:#cfcfcf;
  --footer:#262524;
}
*{box-sizing:border-box;margin:0;padding:0}
html,body{width:1200px;height:3350px;overflow:hidden;background:#fff}
body{font-family:'Montserrat',sans-serif;color:var(--text);position:relative}
.abs{position:absolute}
a{color:inherit;text-decoration:none}

/* header */
.brand{left:112px;top:26px;font-size:21px;font-weight:700;color:var(--ink)}
.contact-item{top:16px;display:flex;align-items:center;gap:14px}
.contact-item .label{font-size:14px;color:var(--muted);font-weight:500}
.contact-item .value{font-size:18px;font-weight:700;color:var(--ink);margin-top:4px;white-space:nowrap}

.nav{left:0;top:83px;width:1200px;height:70px;background:var(--brown);border-bottom:6px solid var(--rust)}
.nav ul{list-style:none;display:flex;position:absolute;left:264px;top:0;height:64px}
.nav li{font-size:15px;font-weight:700;color:#fff;padding:0 26px;display:flex;align-items:center;height:64px}
.nav li.active{background:var(--rust);padding:0 31px}

/* hero */
.hero{left:0;top:153px;width:1200px;height:501px;background:linear-gradient(135deg,#3f4a55 0%,#2a3038 40%,#4b4e52 70%,#262a2e 100%)}
.hero h1{position:absolute;left:0;width:1496px;text-align:center;top:200px;font-size:52px;font-weight:800;color:#fff;text-shadow:2px 3px 6px rgba(0,0,0,.6)}
.hero .sub{position:absolute;left:0;width:1496px;text-align:center;top:272px;font-size:20px;font-weight:700;color:#fff;text-shadow:1px 2px 4px rgba(0,0,0,.6)}
.btn-start{position:absolute;left:670px;top:323px;width:158px;height:45px;background:var(--accent);color:#fff;font-weight:700;font-size:16px;display:flex;align-items:center;justify-content:center}
.slide-arrow{position:absolute;width:47px;height:47px;background:rgba(255,255,255,.25);display:flex;align-items:center;justify-content:center}

.info-band{left:0;top:654px;width:1200px;height:117px;background:var(--brown)}
.info{position:absolute;top:18px;display:flex;gap:20px;color:#fff}
.info .box{width:76px;height:76px;border:1.5px solid #fff;display:flex;align-items:center;justify-content:center;flex:none}
.info h4{font-size:17px;font-weight:700;margin-top:4px}
.info p{font-size:14.5px;line-height:26px;margin-top:2px;font-weight:500}

/* section titles */
.sec-title{position:absolute;left:0;width:1200px;text-align:center}
.sec-title .ghost{font-size:82px;font-weight:800;color:var(--faint);line-height:1}
.sec-title h2{position:absolute;left:0;width:1200px;top:22px;font-size:34px;font-weight:700;color:var(--ink)}

/* about */
.about-col{left:112px;width:451px}
.about-col h3{font-size:22px;font-weight:700;color:var(--brown);line-height:34px}
.about-col p{font-size:15px;line-height:31px;text-align:justify;margin-top:12px}
.btn-read{display:inline-flex;align-items:center;gap:6px;height:39px;padding:0 13px;background:var(--brown);color:#fff;font-size:15px;font-weight:700}
.photo{border:1px solid #ddd;box-shadow:0 2px 6px rgba(0,0,0,.15)}

.rule{left:112px;width:976px;height:1px;background:#9a9a9a}

/* practice */
.card{position:absolute;top:1706px;width:311px;height:378px;border:1.5px solid #e2e2e2;box-shadow:0 2px 6px rgba(0,0,0,.12);background:#fff;text-align:center}
.card.featured{border:2px solid var(--rust)}
.card .icon{width:91px;height:91px;border-radius:50%;border:2px solid var(--rust);margin:33px auto 0;display:flex;align-items:center;justify-content:center}
.card.featured .icon{background:var(--rust)}
.card h3{font-size:19px;font-weight:700;color:var(--ink);margin-top:16px}
.card p{font-size:15px;line-height:28px;color:#666;margin:8px 24px 0}
.card .btn{display:inline-flex;align-items:center;gap:6px;height:43px;padding:0 14px;border:2px solid var(--rust);color:var(--rust);font-weight:700;font-size:15px;margin-top:17px}
.card.featured .btn{background:var(--rust);color:#fff}
.side-arrow{position:absolute;top:1872px;width:47px;height:47px;background:var(--brown);display:flex;align-items:center;justify-content:center}

/* stats & blog */
.stat{position:absolute;width:180px;text-align:center}
.stat .box{width:78px;height:78px;border:2px solid var(--brown);margin:0 auto;display:flex;align-items:center;justify-content:center}
.stat .num{font-size:22px;font-weight:700;color:var(--ink);margin-top:22px}
.stat .lbl{font-size:13.5px;font-weight:600;color:#333;margin-top:4px}
.post{position:absolute;top:2366px;width:277px;height:316px;border:1px solid #ddd;box-shadow:0 2px 6px rgba(0,0,0,.12)}
.post .thumb{height:208px}
.post h3{font-size:20px;font-weight:700;color:var(--ink);line-height:31px;margin:14px 10px 0}
.post .meta{display:flex;justify-content:space-between;font-size:16px;font-weight:500;color:var(--brown);margin:4px 10px 0}
.post .meta span{display:flex;align-items:center;gap:6px}

/* newsletter */
.news-label{left:113px;top:2832px;font-size:20px;font-weight:700;color:var(--ink)}
.news-input{left:286px;top:2824px;width:241px;height:44px;border:1px solid #ccc;font-size:14px;color:#aaa;padding:0 12px;display:flex;align-items:center}
.news-btn{left:537px;top:2824px;width:115px;height:44px;background:var(--brown);color:#fff;font-size:15px;font-weight:700;display:flex;align-items:center;justify-content:center}
.social{position:absolute;top:2822px;width:49px;height:49px;border:2px solid var(--brown);border-radius:50%;display:flex;align-items:center;justify-content:center}

/* footer */
.footer{left:0;top:2912px;width:1200px;height:438px;background:var(--footer);color:#ddd}
.fcol{position:absolute;top:66px}
.fcol h4{font-size:21px;font-weight:700;color:#fff}
.fcol p{font-size:15px;line-height:31px;margin-top:24px;text-align:justify;color:#ddd}
.fcol ul{list-style:none;margin-top:22px}
.fcol li{font-size:15px;line-height:43px;padding-left:18px;position:relative}
.fcol li::before{content:"»";position:absolute;left:0}
.fcol li.wrap{line-height:24px;padding:10px 0 0 18px}
.fcol li.wrap::before{top:10px}
.fbrand{font-size:21px;font-weight:700;color:#fff;line-height:31px;margin-top:22px}
.fcontact{display:flex;gap:14px;font-size:15px;line-height:31px;margin-top:4px}
.fcontact svg{flex:none;margin-top:7px}
.fline{position:absolute;left:112px;top:386px;width:976px;height:1px;background:#555}
.copy{position:absolute;left:0;width:1200px;top:402px;text-align:center;font-size:15px;color:#eee}
</style>
</head>
<body>

<!-- header -->
<div class="abs brand">Meridian Crest Legal Group</div>
<div class="abs contact-item" style="left:542px">
  <svg width="42" height="42" viewBox="0 0 42 42" fill="none" stroke="#b4501b" stroke-width="2.5"><path d="M8 6l7 0 3 9-4 3c2 5 6 9 11 11l3-4 9 3v7c0 2-2 3-4 3C18 38 4 24 4 10c0-2 2-4 4-4z" fill="#b4501b"/><path d="M26 4a12 12 0 0 1 12 12M26 10a6 6 0 0 1 6 6"/></svg>
  <div><div class="label">Call Now</div><div class="value">+1 808 555 0142</div></div>
</div>
<div class="abs contact-item" style="left:780px">
  <svg width="52" height="46" viewBox="0 0 52 46" fill="none" stroke="#b4501b" stroke-width="2.5"><path d="M3 18L26 3l23 15v25H3z"/><path d="M3 18l23 15 23-15M3 43l17-14M49 43L32 29"/><rect x="14" y="10" width="24" height="14" fill="#b4501b" stroke="none"/></svg>
  <div><div class="label">Email Address</div><div class="value" style="font-size:17px">clients@tarnadvocate.example</div></div>
</div>

<nav class="abs nav">
  <ul>
    <li class="active">HOME</li>
    <li>PRACTIVE AREA</li>
    <li>ATTORNEY</li>
    <li>BLOG</li>
    <li>CONTACT US</li>
  </ul>
</nav>

<!-- hero -->
<section class="abs hero" role="img" aria-label="Photo of lawyers in a meeting around a conference table">
  <h1>Meridian Crest Legal Group</h1>
  <div class="sub">Divorce and Personal Injury Lawyers</div>
  <a class="btn-start">GET STARTED</a>
  <div class="slide-arrow" style="left:29px;top:272px"><svg width="16" height="26" viewBox="0 0 16 26"><path d="M13 3L3 13l10 10" stroke="#fff" stroke-width="2.5" fill="none"/></svg></div>
  <div class="slide-arrow" style="left:1118px;top:272px"><svg width="16" height="26" viewBox="0 0 16 26"><path d="M3 3l10 10L3 23" stroke="#fff" stroke-width="2.5" fill="none"/></svg></div>
</section>

<section class="abs info-band">
  <div class="info" style="left:112px">
    <div class="box"><svg width="46" height="32" viewBox="0 0 46 32" fill="none" stroke="#fff" stroke-width="2"><rect x="1" y="1" width="44" height="30"/><path d="M1 1l22 17L45 1M1 31l16-15M45 31L29 16"/></svg></div>
    <div><h4>Case Evaluation</h4><p>Sed ut perspiciatis unde<br>omnis iste natus error</p></div>
  </div>
  <div class="info" style="left:436px">
    <div class="box"><svg width="30" height="42" viewBox="0 0 30 42"><path d="M15 1C7 1 1 7 1 15c0 10 14 26 14 26s14-16 14-26C29 7 23 1 15 1z" fill="#fff"/><circle cx="15" cy="15" r="5" fill="#84290b"/></svg></div>
    <div><h4>Offices Location</h4><p>48-210 Lanakila Avenue, Suite<br>212 Hilo, Hawaii 96720.</p></div>
  </div>
  <div class="info" style="left:809px">
    <div class="box"><svg width="40" height="44" viewBox="0 0 40 44" fill="#fff"><circle cx="20" cy="12" r="10"/><path d="M2 44c0-12 8-18 18-18s18 6 18 18z"/><path d="M17 26l3 10 3-10z" fill="#84290b"/></svg></div>
    <div><h4>LEGAL STAFFS</h4><p>Sed ut perspiciatis unde<br>omnis iste natus error</p></div>
  </div>
</section>

<!-- about -->
<div class="sec-title" style="top:820px">
  <div class="ghost">About Us</div>
  <h2>Who We Are</h2>
</div>
<svg class="abs" style="left:527px;top:877px" width="146" height="28" viewBox="0 0 146 28"><path d="M0 14h58M88 14h58" stroke="#84290b" stroke-width="2"/><circle cx="73" cy="14" r="6" fill="none" stroke="#b4501b" stroke-width="2"/></svg>

<div class="abs about-col" style="top:922px">
  <h3>Lawyers Serving the Big Island &amp;<br>Neighboring Islands</h3>
  <p>The experienced attorneys in the Meridian Crest Legal Group's Hilo, Hawaii office provide clients with a wide range of litigation expertise, including legal claims involving divorce &amp; family, personal injury, toxic exposures, intellectual property, and real estate.</p>
</div>
<a class="abs btn-read" style="left:112px;top:1165px">READ MORE <svg width="13" height="13" viewBox="0 0 13 13"><circle cx="6.5" cy="6.5" r="5.5" fill="none" stroke="#fff" stroke-width="1.6"/><path d="M5 4l3 2.5L5 9" stroke="#fff" stroke-width="1.6" fill="none"/></svg></a>
<div class="abs about-col" style="top:1230px">
  <h3>Nationwide Law Firm Presence</h3>
  <p style="margin-top:8px">Hilo serves as the firm's West Coast headquarters for litigation and representation on behalf of individuals and corporations involved in a wide range of legal matters. The firm and its attorneys are licensed...</p>
</div>
<a class="abs btn-read" style="left:112px;top:1409px">READ MORE <svg width="13" height="13" viewBox="0 0 13 13"><circle cx="6.5" cy="6.5" r="5.5" fill="none" stroke="#fff" stroke-width="1.6"/><path d="M5 4l3 2.5L5 9" stroke="#fff" stroke-width="1.6" fill="none"/></svg></a>

<div class="abs photo" style="left:676px;top:927px;width:339px;height:234px;background:linear-gradient(135deg,#c9d3dc,#6f7f8f 55%,#3e4650)" role="img" aria-label="Photo of business people shaking hands across a desk"></div>
<svg class="abs" style="left:773px;top:1173px" width="146" height="28" viewBox="0 0 146 28"><path d="M0 14h58M88 14h58" stroke="#84290b" stroke-width="2"/><circle cx="73" cy="14" r="6" fill="none" stroke="#b4501b" stroke-width="2"/></svg>
<div class="abs photo" style="left:676px;top:1218px;width:339px;height:233px;background:linear-gradient(135deg,#3a2a1e,#8a6a4e 45%,#d8ccbf 65%,#2e2018)" role="img" aria-label="Photo of hands signing a document beside a gavel and scales"></div>

<div class="abs rule" style="top:1528px"></div>

<!-- practice -->
<div class="sec-title" style="top:1584px">
  <div class="ghost">Practice Area</div>
  <h2>What We Do</h2>
</div>
<svg class="abs" style="left:527px;top:1640px" width="146" height="28" viewBox="0 0 146 28"><path d="M0 14h58M88 14h58" stroke="#84290b" stroke-width="2"/><circle cx="73" cy="14" r="6" fill="none" stroke="#b4501b" stroke-width="2"/></svg>

<div class="side-arrow" style="left:29px"><svg width="16" height="26" viewBox="0 0 16 26"><path d="M13 3L3 13l10 10" stroke="#fff" stroke-width="2.5" fill="none"/></svg></div>
<div class="side-arrow" style="left:1118px"><svg width="16" height="26" viewBox="0 0 16 26"><path d="M3 3l10 10L3 23" stroke="#fff" stroke-width="2.5" fill="none"/></svg></div>

<div class="card" style="left:112px">
  <div class="icon"><svg width="50" height="50" viewBox="0 0 50 50" fill="none" stroke="#b4501b" stroke-width="3"><circle cx="25" cy="25" r="20"/><path d="M25 40V26M25 26l-8-8M25 26l8-8M13 18h6v-6M37 18h-6v-6"/></svg></div>
  <h3>Family &amp; Divorce</h3>
  <p>Our lawyers handle all aspects of family law on the Big Island and neighboring islands. We have more than 70 years..</p>
  <a class="btn">READ MORE <svg width="13" height="13" viewBox="0 0 13 13"><circle cx="6.5" cy="6.5" r="5.5" fill="none" stroke="currentColor" stroke-width="1.6"/><path d="M5 4l3 2.5L5 9" stroke="currentColor" stroke-width="1.6" fill="none"/></svg></a>
</div>
<div class="card featured" style="left:443px">
  <div class="icon"><svg width="50" height="50" viewBox="0 0 50 50" fill="none" stroke="#fff" stroke-width="3"><rect x="8" y="14" width="34" height="26" rx="3"/><path d="M19 14V9h12v5M25 20v14M18 27h14"/></svg></div>
  <h3>Personal Injury</h3>
  <p>Dealing with personal injury and wrongful death claims is hard enough, so the lawyers of MCLG are here to...</p>
  <a class="btn">READ MORE <svg width="13" height="13" viewBox="0 0 13 13"><circle cx="6.5" cy="6.5" r="5.5" fill="none" stroke="currentColor" stroke-width="1.6"/><path d="M5 4l3 2.5L5 9" stroke="currentColor" stroke-width="1.6" fill="none"/></svg></a>
</div>
<div class="card" style="left:775px">
  <div class="icon"><svg width="52" height="52" viewBox="0 0 52 52" fill="none" stroke="#b4501b" stroke-width="3"><circle cx="26" cy="26" r="9"/><path d="M26 4v8M26 40v8M4 26h8M40 26h8M10 10l6 6M36 36l6 6M42 10l-6 6M16 36l-6 6"/></svg></div>
  <h3>Corporate &amp; IP</h3>
  <p>The attorneys at MCLG have been helping Big Island business owners with all their legal needs, so they can...</p>
  <a class="btn">READ MORE <svg width="13" height="13" viewBox="0 0 13 13"><circle cx="6.5" cy="6.5" r="5.5" fill="none" stroke="currentColor" stroke-width="1.6"/><path d="M5 4l3 2.5L5 9" stroke="currentColor" stroke-width="1.6" fill="none"/></svg></a>
</div>

<div class="abs rule" style="top:2188px"></div>

<!-- blog -->
<div class="sec-title" style="top:2244px">
  <div class="ghost">Latest Cases Solved</div>
  <h2>Our Blog</h2>
</div>
<svg class="abs" style="left:527px;top:2300px" width="146" height="28" viewBox="0 0 146 28"><path d="M0 14h58M88 14h58" stroke="#84290b" stroke-width="2"/><circle cx="73" cy="14" r="6" fill="none" stroke="#b4501b" stroke-width="2"/></svg>

<div class="stat" style="left:101px;top:2369px">
  <div class="box"><svg width="52" height="34" viewBox="0 0 52 34" fill="#84290b"><circle cx="26" cy="8" r="7"/><circle cx="10" cy="11" r="5"/><circle cx="42" cy="11" r="5"/><path d="M14 34c0-9 5-14 12-14s12 5 12 14zM0 32c0-7 4-11 10-11 2 0 4 1 5 2-2 3-3 6-3 9zM52 32c0-7-4-11-10-11-2 0-4 1-5 2 2 3 3 6 3 9z"/></svg></div>
  <div class="num">123000+</div><div class="lbl">TRUSTED CLIENTS</div>
</div>
<div class="stat" style="left:296px;top:2369px">
  <div class="box"><svg width="48" height="48" viewBox="0 0 48 48" fill="none" stroke="#84290b" stroke-width="2.2"><rect x="4" y="22" width="34" height="20"/><circle cx="21" cy="32" r="5"/><circle cx="30" cy="12" r="8"/><circle cx="40" cy="20" r="6"/></svg></div>
  <div class="num">$4000k</div><div class="lbl">MONEY PAID</div>
</div>
<div class="stat" style="left:101px;top:2548px">
  <div class="box"><svg width="48" height="44" viewBox="0 0 48 44" fill="none" stroke="#84290b" stroke-width="2.4"><path d="M4 14L24 3l20 11zM4 40h40M2 44h44M10 18v18M19 18v18M29 18v18M38 18v18"/></svg></div>
  <div class="num">97%</div><div class="lbl">SUCCESSFUL CASE</div>
</div>
<div class="stat" style="left:296px;top:2548px">
  <div class="box"><svg width="38" height="46" viewBox="0 0 38 46" fill="#84290b"><path d="M9 20v-7a10 10 0 0 1 20 0v7" fill="none" stroke="#84290b" stroke-width="4"/><rect x="2" y="19" width="34" height="26" rx="3"/><path d="M11 32l6 6 10-11" fill="none" stroke="#fff" stroke-width="3.5"/></svg></div>
  <div class="num">25320</div><div class="lbl">CASE CLOSED</div>
</div>
<div class="abs" style="left:485px;top:2366px;width:1.5px;height:316px;background:var(--rust)"></div>

<article class="post" style="left:507px">
  <div class="thumb" role="img" aria-label="Photo of a lawyer in a suit speaking at a desk" style="background:linear-gradient(135deg,#5c5650,#2f2b28 50%,#8c8279)"></div>
  <h3>Top 10 Things to Do Before Filing for Divorce</h3>
  <div class="meta"><span><svg width="15" height="15" viewBox="0 0 15 15" fill="none" stroke="#84290b" stroke-width="1.6"><rect x="1" y="3" width="13" height="11"/><path d="M1 7h13M4 1v4M11 1v4"/></svg>Jan 23, 2019</span><span><svg width="18" height="14" viewBox="0 0 18 14" fill="none" stroke="#84290b" stroke-width="1.6"><ellipse cx="8" cy="6" rx="7" ry="5"/><path d="M4 10l-2 3 5-2"/></svg>9</span></div>
</article>
<article class="post" style="left:810px">
  <div class="thumb" role="img" aria-label="Photo of a client consulting a lawyer with a gavel on the desk" style="background:linear-gradient(135deg,#e6d2b8,#a67a58 45%,#4a3024)"></div>
  <h3>Top 15 Things to Do During Custody Battle</h3>
  <div class="meta"><span><svg width="15" height="15" viewBox="0 0 15 15" fill="none" stroke="#84290b" stroke-width="1.6"><rect x="1" y="3" width="13" height="11"/><path d="M1 7h13M4 1v4M11 1v4"/></svg>Jan 19, 2019</span><span><svg width="18" height="14" viewBox="0 0 18 14" fill="none" stroke="#84290b" stroke-width="1.6"><ellipse cx="8" cy="6" rx="7" ry="5"/><path d="M4 10l-2 3 5-2"/></svg>8</span></div>
</article>

<div class="abs rule" style="top:2773px"></div>

<!-- newsletter -->
<div class="abs news-label">NEWSLETTER</div>
<div class="abs news-input">Email Address</div>
<a class="abs news-btn">SUBSCRIBE</a>
<div class="social" style="left:876px"><svg width="20" height="20" viewBox="0 0 20 20" fill="none" stroke="#84290b" stroke-width="2"><circle cx="5" cy="10" r="2.5"/><circle cx="15" cy="4" r="2.5"/><circle cx="15" cy="16" r="2.5"/><path d="M7 9l6-4M7 11l6 4"/></svg></div>
<div class="social" style="left:930px"><svg width="20" height="20" viewBox="0 0 20 20" fill="none" stroke="#84290b" stroke-width="2"><path d="M8 12l4-4M9 5l2-2a3.5 3.5 0 0 1 5 5l-2 2M11 15l-2 2a3.5 3.5 0 0 1-5-5l2-2"/></svg></div>
<div class="social" style="left:985px"><svg width="20" height="20" viewBox="0 0 20 20" fill="#84290b"><rect x="5" y="1" width="10" height="5"/><rect x="1" y="7" width="18" height="8" rx="1"/><rect x="5" y="12" width="10" height="7" fill="#fff" stroke="#84290b" stroke-width="1.6"/></svg></div>
<div class="social" style="left:1039px"><svg width="20" height="16" viewBox="0 0 20 16" fill="#84290b"><rect x="0" y="0" width="20" height="16" rx="2"/><path d="M1 2l9 7 9-7" stroke="#fff" stroke-width="1.6" fill="none"/></svg></div>

<!-- footer -->
<footer class="abs footer">
  <div class="fcol" style="left:112px;width:220px">
    <h4>About Us</h4>
    <p>The experienced attorneys in the Meridian Crest Legal Group's Hilo, Hawaii office provide...</p>
    <div class="fbrand">Meridian Crest<br>Legal Group</div>
  </div>
  <div class="fcol" style="left:385px">
    <h4>Important Links</h4>
    <ul><li>Home</li><li>About Us</li><li>Attorneys</li><li>Practice Area</li><li>Blog</li><li>Contact us</li></ul>
  </div>
  <div class="fcol" style="left:625px;width:215px">
    <h4>Practice Area</h4>
    <ul><li>Family &amp; Divorce</li><li>Personal Injury</li><li class="wrap">Corporate &amp; Intellectual Property</li><li style="margin-top:6px">Real Estate</li></ul>
  </div>
  <div class="fcol" style="left:861px;width:235px">
    <h4>Contact Us</h4>
    <div class="fcontact" style="margin-top:20px"><svg width="14" height="18" viewBox="0 0 14 18"><path d="M7 0C3 0 0 3 0 7c0 5 7 11 7 11s7-6 7-11c0-4-3-7-7-7z" fill="#c0550f"/><circle cx="7" cy="7" r="2.5" fill="#262524"/></svg><span>48-210 Lanakila Avenue, Suite 212 Hilo, Hawaii 96720</span></div>
    <div class="fcontact" style="margin-top:8px"><svg width="16" height="16" viewBox="0 0 16 16" fill="#c0550f"><path d="M3 0h3l1.5 4-2 1.5c1 2.5 3 4.5 5.5 5.5L12.5 9l3.5 1.5v3c0 1-1 2-2 2C7 15.5 0 9 0 2c0-1 1-2 2-2z"/></svg><span>+1.808.555.0142</span></div>
    <div class="fcontact" style="margin-top:20px"><svg width="18" height="14" viewBox="0 0 18 14" fill="#c0550f"><rect width="18" height="14" rx="2"/><path d="M1 2l8 6 8-6" stroke="#262524" stroke-width="1.5" fill="none"/></svg><span>clients@tarnadvocate.example</span></div>
  </div>
  <div class="fline"></div>
  <div class="copy">© 2019 Meridian Crest Legal Group | All Rights Reserved</div>
</footer>

</body>
</html>
```